Simple Logo Design for Semi-Clear Plastic Frosted Card stock

Create a business card on frosted plastic. compliment existing logo elements with a tree trunk, roots, or seed at the lower half and the full logo both on the front.

Contact information will go on a solid portion of the back of this design since this card stock is semi-transparent.

It is important to consider this plastic card stock medium in your design. I found helpful tips and guides listed at vellaprint-sample.net: be careful to understand ink printed on plastic cards cannot have too much of a consistent print area or risks peeling and fine lines can easily scratch off.
Updates

2" x 3.5" 20PT Clear Plastic Business cards with Round corners Please get info or templates here: https://www.vellaprint-sample.net/product-detail/2-x-35-20pt-clear-plastic-business-cards-with-round-corners

Target Market(s)

Not for profit- religion

Industry/Entity Type

Business

Must include complementary elements to the existing logo

Font styles to use
Decorative

Colors
000000

Requirements
Must have
• Elements of community, nature and oneness. Such as: seed, roots, tree trunk, etc.
• Three lines of space on the back for Name, Title, Phone Number.
Nice to have
• I like a light use of decorative elements
Should not have
• No eyes, from faces or animals.

```html
<!DOCTYPE html>
<html lang="en">
<head>
<meta charset="utf-8">
<title>Steadfast Path – Business Card</title>
<link rel="stylesheet" href="https://fonts.googleapis.com/css2?family=Questrial&family=Montserrat:wght@600&family=Sorts+Mill+Goudy&family=Arimo&display=swap">
<style>
  :root {
    --backdrop: #e6e2dc;
    --teal: #2f6566;
    --teal-dark: #234f50;
    --leaf-green: #3f7f3a;
    --band-black: #1c1c1c;
    --frost-light: #ecebe8;
    --frost-mid: #d5d4cf;
    --name-green: #2f6b2c;
    --ink: #2b2b2b;
    --tagline: #4f5a55;
  }
  * { margin: 0; padding: 0; box-sizing: border-box; }
  html, body {
    width: 1200px; height: 970px; overflow: hidden;
    background: var(--backdrop);
  }
  .card {
    position: absolute; left: 80px; top: 174px;
    width: 1040px; height: 622px;
    border-radius: 24px; overflow: hidden;
    box-shadow: 0 10px 30px rgba(0,0,0,0.18);
  }
  .card-face { position: absolute; inset: 0; }
  .brand-mark {
    position: absolute; left: 380px; top: 72px;
    width: 116px; height: 116px; border-radius: 50%;
    background: var(--teal);
  }
  .brand-name {
    position: absolute; left: 186px; top: 206px;
    font-family: "Questrial", sans-serif;
    font-size: 54px; line-height: 64px; letter-spacing: 1px;
    color: var(--teal); white-space: nowrap;
  }
  .brand-tagline {
    position: absolute; left: 236px; top: 276px;
    font-family: "Montserrat", sans-serif; font-weight: 600;
    font-size: 17px; letter-spacing: 0.5px;
    color: var(--tagline); white-space: nowrap;
  }
  .person-name {
    position: absolute; right: 157px; top: 326px;
    font-family: "Sorts Mill Goudy", serif;
    font-size: 42px; line-height: 50px; color: var(--name-green); white-space: nowrap;
  }
  .divider {
    position: absolute; left: 120px; top: 401px;
    width: 486px; height: 2px; background: var(--band-black);
  }
  .person-title {
    position: absolute; right: 162px; top: 386px;
    font-family: "Arimo", sans-serif;
    font-size: 26px; line-height: 32px; color: var(--band-black); white-space: nowrap;
  }
  .contact-list {
    position: absolute; left: 196px; top: 432px;
    list-style: none;
    font-family: "Arimo", sans-serif; font-size: 26px; color: var(--ink);
  }
  .contact-item {
    display: flex; align-items: center; gap: 22px;
    height: 39px;
  }
  .contact-icon { width: 20px; height: 20px; flex: none; }
</style>
</head>
<body>
  <div class="card">
    <svg class="card-face" width="1040" height="622" viewBox="0 0 1040 622">
      <defs>
        <linearGradient id="frost" x1="0" y1="0" x2="0" y2="1">
          <stop offset="0" stop-color="var(--frost-light)"/>
          <stop offset="1" stop-color="var(--frost-mid)"/>
        </linearGradient>
        <linearGradient id="side" x1="0" y1="0" x2="0" y2="1">
          <stop offset="0" stop-color="var(--teal)"/>
          <stop offset="1" stop-color="var(--teal-dark)"/>
        </linearGradient>
      </defs>
      <rect class="side-panels" width="1040" height="622" fill="url(#side)"/>
      <path class="black-band" d="M117 0 Q40 311 117 622 L905 622 Q995 311 905 0 Z" fill="var(--band-black)"/>
      <path class="green-band" d="M135 0 Q70 311 135 622 L890 622 Q970 311 890 0 Z" fill="var(--leaf-green)"/>
      <path class="frosted-window" role="img" aria-label="Frosted card surface with a faint damask pattern"
            d="M151 0 Q95 311 151 622 L875 622 Q950 311 875 0 Z" fill="url(#frost)"/>
    </svg>

    <div class="brand-mark"></div>
    <div class="brand-name">STEADFAST PATH</div>
    <div class="brand-tagline">WISDOM, FELLOWSHIP &amp; HARMONY</div>

    <div class="person-name">Martin Ellery</div>
    <div class="divider"></div>
    <div class="person-title">Managing Director</div>

    <ul class="contact-list">
      <li class="contact-item">
        <svg class="contact-icon" viewBox="0 0 20 20"><rect width="20" height="20" rx="2" fill="var(--leaf-green)"/><path d="M5 8 Q10 4 15 8 L13 10 L11 8.5 L9 8.5 L7 10 Z M6 11 H14 V15 H6 Z" fill="#fff"/></svg>
        <span>0400 123 456</span>
      </li>
      <li class="contact-item">
        <svg class="contact-icon" viewBox="0 0 20 20"><rect width="20" height="20" rx="2" fill="var(--leaf-green)"/><rect x="7" y="3.5" width="6" height="13" rx="1" fill="#fff"/><rect x="8" y="5" width="4" height="7" fill="var(--leaf-green)"/></svg>
        <span>0400 123 457</span>
      </li>
      <li class="contact-item">
        <svg class="contact-icon" viewBox="0 0 20 20"><rect width="20" height="20" rx="2" fill="var(--leaf-green)"/><rect x="4" y="6" width="12" height="8" fill="#fff"/><path d="M4 6 L10 11 L16 6" fill="none" stroke="var(--leaf-green)" stroke-width="1.2"/></svg>
        <span>martin@ellerymail.com</span>
      </li>
      <li class="contact-item">
        <svg class="contact-icon" viewBox="0 0 20 20"><rect width="20" height="20" rx="2" fill="var(--leaf-green)"/><circle cx="10" cy="10" r="5.5" fill="none" stroke="#fff" stroke-width="1.4"/><path d="M4.5 10 H15.5 M10 4.5 Q7 10 10 15.5 Q13 10 10 4.5" fill="none" stroke="#fff" stroke-width="1.1"/></svg>
        <span>www.martinellery.com</span>
      </li>
    </ul>
  </div>
</body>
</html>
```